Tobble *

To create online free mini games website. There’re will be up to 100 games on website with 6-8 categories. Domain name is not selected yet.

Number of Pages Required

1 page

```html
<!DOCTYPE html>
<html lang="en">
<head>
<meta charset="utf-8">
<title>Tobble Games</title>
<link rel="stylesheet" href="https://fonts.googleapis.com/css2?family=Lilita+One&family=Open+Sans:wght@400;600&display=swap">
<style>
:root{
  --red:#c0111f;
  --beige:#f2e6da;
  --navy:#123e92;
  --deep:#1f2d48;
  --orange:#f59a12;
  --orange-dark:#e9780a;
  --line:#d6d0c9;
  --text:#222;
  --footer:#2b2b2b;
  --white:#fff;
}
*{box-sizing:border-box;margin:0;padding:0}
html,body{width:865px;height:1200px;overflow:hidden}
body{position:relative;background:var(--beige);font-family:"Open Sans",sans-serif;color:var(--text)}
.abs{position:absolute}
.hero-art{position:absolute;left:0;top:0;width:865px;height:380px;
  background:radial-gradient(ellipse at 40% 60%,#6d9a3e 0%,rgba(109,154,62,0) 35%),linear-gradient(180deg,#a9cdbf 0%,#8fb7a9 40%,#6f8f7e 75%,#d9dfd8 100%)}
.band{position:absolute;left:0;top:330px;width:865px;height:120px}
.logo{position:absolute;left:96px;top:16px;font-family:"Lilita One",sans-serif;font-size:44px;color:var(--orange);line-height:1}
.hero-title{position:absolute;left:0;width:865px;top:172px;text-align:center;font-family:"Lilita One",sans-serif;font-size:34px;color:var(--white);text-shadow:0 0 3px var(--navy),0 2px 0 var(--navy)}
.btn{display:inline-block;background:linear-gradient(#ffb12a,var(--orange-dark));color:var(--red);font-family:"Lilita One",sans-serif;border:3px solid #ffd36a;border-radius:30px;text-align:center}
.hero-btn{position:absolute;left:383px;top:222px;width:100px;height:36px;line-height:30px;font-size:16px}
.arrow{position:absolute;top:186px}
.nav{position:absolute;left:95px;top:393px;display:flex;gap:0}
.nav a{color:var(--white);text-decoration:none;font-size:12px;padding:0 13px;height:23px;line-height:23px}
.nav a.active{background:var(--orange);border-radius:2px}
.search{position:absolute;left:585px;top:393px;width:185px;height:23px;background:var(--white);border-radius:2px;font-size:9px;color:#888;padding-left:10px;line-height:23px}
.search svg{position:absolute;right:7px;top:6px}
.heading{position:absolute;font-family:"Lilita One",sans-serif;font-size:20px;color:var(--navy);line-height:1}
.panel{position:absolute;background:var(--white);border:1px solid var(--line)}
.grid{position:absolute;left:6px;top:14px;display:flex;gap:7px}
.card{width:101px;text-align:center;font-size:8px}
.thumb{width:101px;height:86px;border:2px solid var(--navy);margin-bottom:14px}
.tabs{position:absolute;left:95px;top:891px;display:flex;gap:2px}
.tabs span{width:61px;height:27px;line-height:27px;background:#c9c9c9;color:#444;font-size:8.5px;text-align:center}
.tabs span.active{background:var(--navy);color:var(--white)}
.tabs-rule{position:absolute;left:95px;top:915px;width:438px;height:3px;background:var(--navy)}
.gotd{position:absolute;left:555px;top:524px;width:215px;height:138px;background:linear-gradient(160deg,#c2401f 0%,#7a2a22 40%,#1e2a3a 100%)}
.gotd-title{position:absolute;left:16px;bottom:10px;font-family:"Lilita One",sans-serif;font-size:19px;color:var(--white)}
.gotd-btn{position:absolute;right:13px;bottom:6px;width:76px;height:28px;line-height:22px;font-size:13px}
.recent{position:absolute;left:555px;top:720px;width:215px;height:225px;background:var(--deep)}
.recent-item{height:75px;display:flex;align-items:center;padding-left:13px;border-bottom:1px solid #34425e}
.recent-item:last-child{border-bottom:0}
.recent-thumb{width:70px;height:47px;margin-right:12px;flex:none}
.recent-item p{font-size:7.8px;line-height:14px;color:var(--white);width:115px}
.tags{position:absolute;left:555px;top:992px;width:215px;height:62px;background:var(--white);border:1px solid var(--line);color:#666}
.tags span{position:absolute;line-height:1}
.footer{position:absolute;left:0;top:1108px;width:865px;height:92px}
.footer-links{position:absolute;left:95px;top:1147px;font-size:8px;color:#ccc}
.footer-links span{padding:0 6px}
.copy{position:absolute;left:95px;top:1166px;font-size:8px;color:#ccc}
.social{position:absolute;top:1153px;width:18px;height:18px;border-radius:50%}
</style>
</head>
<body>
<div class="hero-art" role="img" aria-label="Fantasy landscape with floating rocky islands, waterfalls and misty mountains"></div>
<svg class="band" width="865" height="120" viewBox="0 0 865 120">
  <path d="M0 10 Q432 70 865 10 L865 100 Q432 125 0 100 Z" fill="var(--red)"/>
</svg>
<div class="logo">Tobble Games</div>
<svg class="arrow" style="left:38px" width="14" height="20" viewBox="0 0 14 20"><path d="M11 2 L3 10 L11 18" stroke="#fff" stroke-width="3" fill="none"/></svg>
<svg class="arrow" style="left:813px" width="14" height="20" viewBox="0 0 14 20"><path d="M3 2 L11 10 L3 18" stroke="#fff" stroke-width="3" fill="none"/></svg>
<div class="hero-title">Suspendisse elit ligula</div>
<span class="btn hero-btn">Play Now</span>

<nav class="nav">
  <a class="active">Action</a><a>Casino</a><a>Adventure</a><a>Puzzle</a><a>Driving</a><a>Sports</a><a>Bubble</a>
</nav>
<div class="search">Search
  <svg width="11" height="11" viewBox="0 0 11 11"><circle cx="4.5" cy="4.5" r="3.3" stroke="#111" stroke-width="1.6" fill="none"/><path d="M7 7 L10 10" stroke="#111" stroke-width="1.8"/></svg>
</div>

<div class="heading" style="left:95px;top:498px">Editor’s Pick</div>
<div class="panel" style="left:95px;top:524px;width:438px;height:138px">
  <div class="grid">
    <div class="card"><div class="thumb" role="img" aria-label="Platform game level with coins" style="background:linear-gradient(#7fd3f0,#b5663a)"></div>Donec quis</div>
    <div class="card"><div class="thumb" role="img" aria-label="Pixel landscape with clouds and mushrooms" style="background:linear-gradient(#8fd0ee 60%,#3d8c2c 80%,#6b3e20)"></div>Phasellus</div>
    <div class="card"><div class="thumb" role="img" aria-label="Floating rock at golden sunset" style="background:linear-gradient(#f3c53a,#8e7a2c 70%,#4b4020)"></div>Aliquam</div>
    <div class="card"><div class="thumb" role="img" aria-label="Pixel city street with cars" style="background:linear-gradient(#9ab7d8,#7aa36a 45%,#9a9a9a 60%,#6d6d6d)"></div>Maecenas</div>
  </div>
</div>

<div class="heading" style="left:555px;top:498px">Game of Day</div>
<div class="gotd" role="img" aria-label="Dark cave scene with a small warrior and glowing crystals">
  <div class="gotd-title">Fusce porta</div>
  <span class="btn gotd-btn">Play Now</span>
</div>

<div class="heading" style="left:95px;top:694px">Hot Games</div>
<div class="panel" style="left:95px;top:720px;width:438px;height:138px">
  <div class="grid">
    <div class="card"><div class="thumb" role="img" aria-label="Glowing blue magical figure" style="background:radial-gradient(circle at 60% 60%,#5fc3ff,#123a7a 70%)"></div>Donec quis</div>
    <div class="card"><div class="thumb" role="img" aria-label="Pixel platform level with bricks" style="background:linear-gradient(#6fc1e8,#7a3d22 55%,#3a1d12)"></div>Phasellus</div>
    <div class="card"><div class="thumb" role="img" aria-label="Platform level with coins and door" style="background:linear-gradient(#7fd3f0,#8a3b2a 50%,#4a1e15)"></div>Aliquam</div>
    <div class="card"><div class="thumb" role="img" aria-label="Adventurer holding a torch in darkness" style="background:radial-gradient(circle at 40% 20%,#c77a2a,#1e2030 65%)"></div>Maecenas</div>
  </div>
</div>

<div class="tabs"><span class="active">Action</span><span>Casino</span><span>Adventure</span><span>Puzzle</span><span>Driving</span><span>Sports</span><span>Bubble</span></div>
<div class="tabs-rule"></div>
<div class="panel" style="left:95px;top:918px;width:438px;height:136px;border-top:0">
  <div class="grid" style="top:13px">
    <div class="card"><div class="thumb" role="img" aria-label="Cartoon hills and desert" style="background:linear-gradient(#9fe0e8,#d48a6a 55%,#6aa03a 80%,#b5632d)"></div>Donec quis</div>
    <div class="card"><div class="thumb" role="img" aria-label="Pirate maze puzzle board" style="background:linear-gradient(#f4e3b2,#7ec8d0 50%,#e0a040)"></div>Phasellus</div>
    <div class="card"><div class="thumb" role="img" aria-label="Mystical figure under a night sky" style="background:radial-gradient(circle at 20% 20%,#7fa0a0,#0f2224 60%)"></div>Aliquam</div>
    <div class="card"><div class="thumb" role="img" aria-label="Armed soldiers in combat" style="background:linear-gradient(#6d7480,#2c3038)"></div>Maecenas</div>
  </div>
</div>

<div class="heading" style="left:555px;top:694px">Recently Visited</div>
<div class="recent">
  <div class="recent-item"><div class="recent-thumb" role="img" aria-label="Dark fantasy creature artwork" style="background:linear-gradient(#5a5a5a,#1e1e1e)"></div><p>Vestibulum pharetra diam ex, in posuere purus efficitur ac. Mauris placerat eros.</p></div>
  <div class="recent-item"><div class="recent-thumb" role="img" aria-label="Armored blue hero artwork" style="background:radial-gradient(circle,#4a6ad0,#12182e 70%)"></div><p>Vestibulum pharetra diam ex, in posuere purus efficitur ac. Mauris placerat eros.</p></div>
  <div class="recent-item"><div class="recent-thumb" role="img" aria-label="Card battle game screen" style="background:linear-gradient(#2a3a70,#8a3020 60%,#1a1a2a)"></div><p>Vestibulum pharetra diam ex, in posuere purus efficitur ac. Mauris placerat eros.</p></div>
</div>

<div class="heading" style="left:555px;top:966px">Tags</div>
<div class="tags">
  <span style="left:10px;top:9px;font-size:11px">Gun</span>
  <span style="left:11px;top:26px;font-size:8px">Flight</span>
  <span style="left:41px;top:17px;font-size:14px">Bike</span>
  <span style="left:81px;top:16px;font-size:11px">Sword</span>
  <span style="left:78px;top:32px;font-size:7px">Puzzle</span>
  <span style="left:122px;top:7px;font-size:7px">Car</span>
  <span style="left:127px;top:20px;font-size:14px">Chess</span>
  <span style="left:166px;top:6px;font-size:11px">Army</span>
  <span style="left:11px;top:42px;font-size:11px">Shooting</span>
  <span style="left:70px;top:46px;font-size:7.5px">Adventure</span>
  <span style="left:135px;top:41px;font-size:11px">Sports</span>
  <span style="left:180px;top:45px;font-size:6.5px">Treasure</span>
</div>

<svg class="footer" width="865" height="92" viewBox="0 0 865 92">
  <path d="M0 24 Q432 -8 865 24 L865 92 L0 92 Z" fill="var(--footer)"/>
</svg>
<div class="footer-links">About Us<span>|</span>Contact Us<span>|</span>Terms &amp; Conditions</div>
<div class="copy">Copyright © 2018 Tobble Games.&nbsp;&nbsp;All rights reserved.</div>
<div class="social" style="left:679px;background:#3b5a9a"></div>
<div class="social" style="left:703px;background:#2aa3e0"></div>
<div class="social" style="left:727px;background:#d9432f"></div>
<div class="social" style="left:751px;background:#c8202b"></div>
</body>
</html>
```